Computer consultant business card

Bexil Software is a newly started computer consulting company. It's a small one-man company that provides mostly Vornix applications but also websites in collaboration with designers. I'm running this company on the side of full time university studies.

I want the final design to be clean and memorable. Be creative! :)

Some inspiration:
http://www.pixelmarta.com/design/48317
http://www.pixelmarta.com/design/2739164/business-card-design-by-frostlynk
http://www.pixelmarta.com/design/604281/business-card-design-by-koralind-vestrabanu

See attachment for my company logo.
Updates

I would like to thank everyone for submitting! I'll need a couple of days to review and ultimately select a design.

Target Market(s)

Non-technical entrepreneurs and small companies.

Industry/Entity Type

University

Requirements
Must have
• My company logo.
In any way, both colors from my logo.
First- and last name, e-mail and phone number.
Double-sided design.
Nice to have
• Something creative with the symbol in my logo

```html
<!DOCTYPE html>
<html lang="en">
<head>
<meta charset="utf-8">
<title>Tovrik – Business Card</title>
<link href="https://fonts.googleapis.com/css2?family=Arimo:wght@400;700&display=swap" rel="stylesheet">
<style>
  :root {
    --brand-blue: #1f7bf2;
    --brand-charcoal: #333131;
    --metal-light: #e6e6e6;
    --metal-mid: #a9a9a9;
    --metal-dark: #2b2b2b;
    --stage: #f1f1f1;
    --text-muted: #3a3a3a;
  }
  * { box-sizing: border-box; margin: 0; padding: 0; }
  html, body {
    width: 1200px;
    height: 785px;
    overflow: hidden;
    background: var(--stage);
    font-family: "Arimo", Arial, sans-serif;
  }
  .stage {
    width: 1200px;
    height: 785px;
    display: flex;
    align-items: center;
    justify-content: center;
    gap: 40px;
  }
  .card {
    position: relative;
    width: 540px;
    height: 310px;
    background: linear-gradient(180deg, var(--metal-light) 0%, #cfcfcf 35%, var(--metal-mid) 60%, var(--metal-dark) 100%);
    box-shadow: 0 6px 18px rgba(0,0,0,0.25);
    overflow: hidden;
  }

  /* Front */
  .brand {
    position: absolute;
    left: 44px;
    top: 44px;
    display: flex;
    align-items: center;
    gap: 16px;
  }
  .brand-dot {
    width: 60px;
    height: 60px;
    border-radius: 50%;
    background: var(--brand-blue);
    flex: none;
  }
  .brand-name {
    font-size: 76px;
    font-weight: 400;
    line-height: 1;
    color: var(--brand-charcoal);
  }
  .holder {
    position: absolute;
    left: 62px;
    top: 214px;
    line-height: 1.05;
  }
  .holder-first {
    font-size: 20px;
    font-weight: 700;
    color: var(--brand-blue);
  }
  .holder-last {
    font-size: 18px;
    color: var(--text-muted);
  }
  .contact {
    position: absolute;
    left: 318px;
    top: 178px;
    padding-left: 14px;
    border-left: 2px solid var(--brand-blue);
    font-size: 13px;
    color: var(--text-muted);
    line-height: 1.5;
  }
  .contact-row {
    display: flex;
    align-items: center;
    gap: 6px;
  }
  .contact-icon {
    width: 11px;
    height: 11px;
    fill: var(--brand-blue);
    flex: none;
  }
  .contact-address { margin-top: 6px; }

  /* Back */
  .back-brand {
    position: absolute;
    inset: 0;
    display: flex;
    align-items: center;
    justify-content: center;
    gap: 18px;
  }
  .back-dot {
    width: 80px;
    height: 80px;
    border-radius: 50%;
    background: var(--brand-blue);
    flex: none;
  }
  .back-name {
    font-size: 96px;
    font-weight: 400;
    line-height: 1;
    color: var(--brand-charcoal);
  }
</style>
</head>
<body>
<main class="stage">
  <section class="card card-front" aria-label="Business card front">
    <div class="brand">
      <span class="brand-dot"></span>
      <span class="brand-name">tovrik</span>
    </div>
    <div class="holder">
      <p class="holder-first">First Name</p>
      <p class="holder-last">Last Name</p>
    </div>
    <div class="contact">
      <p class="contact-row">
        <svg class="contact-icon" viewBox="0 0 12 12" aria-hidden="true"><path d="M2.5 0.5l2 2-1.2 1.6a7 7 0 0 0 4.6 4.6l1.6-1.2 2 2-1.5 2A10 10 0 0 1 0.5 2z"/></svg>
        0912 384765
      </p>
      <p class="contact-row">
        <svg class="contact-icon" viewBox="0 0 12 12" aria-hidden="true"><path d="M0 2h12v8H0z M0.8 2.6l5.2 4 5.2-4" stroke="#e6e6e6" stroke-width="0.8"/></svg>
        info@tovrik.com
      </p>
      <p class="contact-address">00, Complex name<br>City, State 0042</p>
    </div>
  </section>

  <section class="card card-back" aria-label="Business card back">
    <div class="back-brand">
      <span class="back-dot"></span>
      <span class="back-name">tovrik</span>
    </div>
  </section>
</main>
</body>
</html>
```